Coral Reach Yachting Flyer

Coral Reach Yachting (.com) is a high end luxury and private charter company in the Cayman Islands. All info can be found on our webiste. I currently have a 4 panel roll fold flyer (Can supply working file). I am looking for a new fresh look but also need some changes as we have changes some boats, added some new charter ideas etc.

Between our website and current flyer I think the designer will get the idea. I Welcome new and fresh, I do not need it to match current website, as I may get that changed to.

We are looking for high end and simple/clean and comunicate reliability and professional with a hint of fun in the sun of course. Not whacky and tacky!!

The current PDF's of the current flyer needs a fair bit of changing (For example scuba diving panel will come out and go into a new 1 panel flyer.) I will need 3-4 other flyers too, and a bunch of other stuff in future for new businesses, but starting with this one so I can pick a designer (This is my 1st go with pixel bazaar, always did my own work, but am too busy and am not very good with creativity)

I have logo, support pictures, etc. Have uploaded the basics can email more info and changes after I find a designer. Lots of our boat pictures can be found at http://coralreachyachting.example/downloads/maple.zip

Also, we want a panel dedicated to wavedart.example as our big boat now has one onboard and our smaller boat (23') will have two and that will be a dedicated panel (Replace scuba) offering a "Wavedart Ultra Reef trip" (I will supply more info on that, once I pick a designer).

Target Market(s)

High end groups. The groups or families that will spend more to get more!!

Industry/Entity Type

It Company

```html
<!DOCTYPE html>
<html lang="en">
<head>
<meta charset="utf-8">
<title>Coral Reach Yachting – Roll Fold Flyer</title>
<link rel="stylesheet" href="https://fonts.googleapis.com/css2?family=Arimo:wght@400;700&family=Open+Sans:wght@400;600&display=swap">
<style>
  :root {
    --navy: #2e3192;
    --cyan: #3ec1e0;
    --sky-text: #6f9fdc;
    --list-blue: #4a7cc4;
    --white: #ffffff;
    --ink: #1a1a1a;
    --gold: #f2b21a;
    --stage: #ecebe8;
    --sea-deep: #1b8fa8;
    --sea-light: #6fd3e0;
  }
  * { margin: 0; padding: 0; box-sizing: border-box; }
  html, body { width: 1200px; height: 802px; overflow: hidden; background: var(--stage); }
  .flyer {
    position: absolute; left: 100px; top: 97px;
    width: 1000px; height: 608px;
    background: var(--white);
    font-family: "Arimo", Arial, sans-serif;
  }
  .panel { position: absolute; top: 0; width: 250px; height: 604px; overflow: hidden; }
  .panel--why { left: 0; background: var(--navy); }
  .panel--activities { left: 250px; background: var(--white); }
  .panel--about { left: 500px; background: var(--white); }
  .panel--cover { left: 750px; background: var(--navy); }
  .gold-rule { position: absolute; left: 0; top: 604px; width: 1000px; height: 4px; background: var(--gold); }

  .block, .photo { position: absolute; }
  .photo { background: linear-gradient(170deg, #bfe6f4 0%, var(--sea-light) 40%, var(--sea-deep) 100%); }
  .photo--deck { background: linear-gradient(160deg, #a9c8dc 0%, #e9eef1 55%, #7e98a8 100%); }
  .photo--portrait { background: linear-gradient(160deg, #87b7d6 0%, #3d5666 60%, #2a3440 100%); }
  .block--cyan { background: var(--cyan); }
  .block--navy { background: var(--navy); }
  .block--white { background: var(--white); }

  .why-title { position: absolute; left: 19px; top: 196px; font: 400 14px "Open Sans", sans-serif; color: var(--sky-text); }
  .why-copy { position: absolute; left: 17px; top: 225px; width: 218px; font-size: 9.2px; line-height: 12.6px; font-weight: 700; color: var(--white); }

  .activities-title { position: absolute; left: 29px; top: 49px; width: 200px; font: 400 14.5px/19px "Open Sans", sans-serif; color: var(--list-blue); }
  .activities-list { position: absolute; left: 30px; top: 94px; list-style: none; font-size: 10.4px; line-height: 14.4px; font-weight: 700; color: var(--ink); }
  .activities-list li::before { content: "•"; color: var(--list-blue); margin-right: 6px; }

  .about-title { position: absolute; left: 27px; top: 18px; font: 400 14px "Open Sans", sans-serif; color: var(--navy); }
  .about-subtitle { position: absolute; left: 27px; top: 35px; font: 400 8.4px "Open Sans", sans-serif; color: var(--navy); }
  .about-copy { position: absolute; left: 27px; width: 200px; font: 400 8.3px/11.4px "Open Sans", sans-serif; color: var(--white); text-align: justify; }
  .about-copy p + p { margin-top: 11px; }
  .contact { position: absolute; left: 26px; top: 529px; color: var(--white); font-weight: 700; }
  .contact-call { font-size: 14.5px; line-height: 19px; }
  .contact-line { font-size: 11.6px; line-height: 17px; }

  .cover-headline { position: absolute; left: 835px; top: 317px; font: 400 25px/35px "Arimo", sans-serif; color: var(--white); }
  .brand { position: absolute; left: 751px; top: 428px; width: 249px; height: 127px; background: var(--white); display: flex; align-items: center; justify-content: center; gap: 8px; }
  .brand-mark { width: 14px; height: 14px; border-radius: 50%; background: var(--gold); }
  .brand-name { font: 700 15px "Arimo", sans-serif; color: var(--navy); letter-spacing: .3px; }
</style>
</head>
<body>
<main class="flyer">
  <section class="panel panel--why">
    <div class="photo" style="left:0;top:0;width:250px;height:167px" role="img" aria-label="Sport boat cruising on turquoise sea"></div>
    <h2 class="why-title">Why Choose us?</h2>
    <p class="why-copy">We are a Caymanian owned company striving to offer something different to locals and tourists alike. For the past 30 years the founder of this company has enjoyed the unparalleled beauty of the Cayman Islands &amp; surrounding waters. Water skiing, diving, Rum Point..</p>
    <div class="photo" style="left:82px;top:342px;width:168px;height:114px" role="img" aria-label="Swimmer with a stingray in clear water"></div>
    <div class="block block--cyan" style="left:0;top:458px;width:82px;height:146px"></div>
    <div class="photo" style="left:82px;top:456px;width:103px;height:71px" role="img" aria-label="Boat bow over blue water"></div>
  </section>

  <section class="panel panel--activities">
    <h2 class="activities-title">Things to do with us, in Grand Cayman</h2>
    <ul class="activities-list">
      <li>Swimming and Snorkeling</li>
      <li>Bioluminescence Night Diving</li>
      <li>USS Kittiwake Snorkelling</li>
      <li>Deep Sea Fishing</li>
      <li>Starfish Point</li>
      <li>Harbor Bbq Tuesdays</li>
      <li>Purchase a vacation home</li>
      <li>Family Beach Portraits</li>
      <li>Rent your own vacation villa</li>
    </ul>
    <div class="photo" style="left:128px;top:262px;width:122px;height:84px" role="img" aria-label="Guest relaxing on a boat deck"></div>
    <div class="photo photo--deck" style="left:0;top:302px;width:128px;height:154px" role="img" aria-label="Helm and seats on a charter boat"></div>
    <div class="photo photo--portrait" style="left:128px;top:346px;width:122px;height:110px" role="img" aria-label="Angler holding a caught fish"></div>
    <div class="photo photo--deck" style="left:0;top:458px;width:142px;height:104px" role="img" aria-label="Charter boat moored at the dock"></div>
    <div class="photo" style="left:143px;top:458px;width:107px;height:69px" role="img" aria-label="Boat wake on open water"></div>
    <div class="block block--cyan" style="left:143px;top:527px;width:48px;height:77px"></div>
  </section>

  <section class="panel panel--about">
    <div class="block block--cyan" style="left:0;top:0;width:250px;height:155px"></div>
    <h2 class="about-title">Cayman Islands</h2>
    <p class="about-subtitle">Luxury Yachts &amp; Private Charters</p>
    <div class="about-copy" style="top:58px">
      <p>Privacy is a luxury, but yet a necessity in every person's life. Have you ever been on one of those large excursion boats that carry hundreds of people and you can't wait to get off! Look no further, Coral Reach Yachting was built on the premise of pure privacy to do what you want and when you want it</p>
    </div>
    <div class="photo" style="left:0;top:160px;width:250px;height:152px" role="img" aria-label="Guests riding an underwater scooter in the sea"></div>
    <div class="block block--cyan" style="left:0;top:318px;width:250px;height:207px"></div>
    <div class="about-copy" style="top:349px">
      <p>Avoid those overloaded tours and get the service and attention you and your family deserve! We have many boats to choose from and can meet every budget.</p>
      <p>We offer daily private charters the most impressive spots Caymans water has to offer, Stingray City Sandbar, Snorkeling on the Barrier reef, Starfish Point, USS Kittiwake and Seven Mile Beach just to name a few, you pick the boat, just tell us where you want to go</p>
    </div>
    <div class="block block--navy" style="left:0;top:525px;width:250px;height:79px"></div>
    <div class="contact">
      <p class="contact-call">Call us now!</p>
      <p class="contact-line">345-555-0142</p>
      <p class="contact-line">info@CoralReachYachting.example</p>
      <p class="contact-line">www.coralreachyachting.example</p>
    </div>
  </section>

  <section class="panel panel--cover">
    <div class="photo" style="left:108px;top:0;width:142px;height:95px" role="img" aria-label="Motor yacht under sail on a calm sea"></div>
    <div class="photo" style="left:0;top:95px;width:166px;height:105px" role="img" aria-label="Sport boat speeding across the water"></div>
    <div class="photo" style="left:85px;top:200px;width:165px;height:110px" role="img" aria-label="View of the sea from a boat bow"></div>
  </section>

  <h1 class="cover-headline">Show Your<br>Love<br>With Us</h1>
  <div class="brand">
    <span class="brand-mark"></span>
    <span class="brand-name">Coral Reach Yachting</span>
  </div>

  <div class="gold-rule"></div>
</main>
</body>
</html>
```